Australian Based Web Development Company Needs a Fresh New Modern Look (logo and responsive website)

We are Coral Web Development, an Australian based web development company looking to give our company a fresh, new and modern look.

We tend to deal with small to medium sized businesses, and want to convey the message that we are professional and capable of developing a solution to any need or problem.

Our specialty is custom development applications, such as, intranets, integration software, and client portals.

We have recently started mobile application development as well (iOS and Android).

You can view our current logo and website on https://www.coralwebdevelopment.example/

As we are looking for both a logo and a website design, we may decide to have the website design completed by a different designer to the winning logo designer.

Target Market(s)

Small to medium enterprise businesses

Industry/Entity Type

It Company

Logo Text

Coral Web Development

Number of Pages Required

2 page

Logo styles of interest
Abstract Logo
Wordmark Logo
Font styles to use
Sans Serif

Colors
85cae6
33b8a4

Requirements
Must have
• Website design - a responsive layout (960-1000px content width), and background image/texture of 2,560px wide. A home page design, and a generic content page design.
• Colours - we like blues, greens (more blue-green like teal) and grey, but we are open to seeing other colours if you feel appropriate.
Nice to have
• Website design - Two websites I like the design style is http://www.mavonstack.example/ and https://www.pilvo.example/au/accounting-software/

```html
<!DOCTYPE html>
<html lang="en">
<head>
<meta charset="utf-8">
<title>Coral Web Development</title>
<link rel="stylesheet" href="https://fonts.googleapis.com/css2?family=Open+Sans:wght@300;400;600;700&family=Oswald:wght@300;400&display=swap">
<style>
:root{
  --teal:#33b8a4;
  --teal-dark:#2aa592;
  --sky:#85cae6;
  --ink:#333a40;
  --text:#6b6b6b;
  --muted:#8d8d8d;
  --ring:#dde3f3;
  --footer:#2e2e2e;
  --footer-bar:#262626;
}
*{box-sizing:border-box;margin:0;padding:0}
html,body{width:1200px;height:3169px;overflow:hidden;background:#fff}
body{font-family:"Open Sans",Arial,sans-serif;color:var(--text);position:relative}

/* header */
.site-header{position:absolute;left:0;top:0;width:1200px;height:89px;background:linear-gradient(#fff,#f1f1f1)}
.brand{position:absolute;left:139px;top:16px;font-weight:600;color:var(--teal);line-height:1}
.brand .name{font-size:34px;letter-spacing:1px}
.brand .sub{font-size:11px;letter-spacing:3px;margin-top:5px;text-transform:uppercase}
.tagline{position:absolute;left:623px;top:27px;width:450px;border-left:5px solid var(--teal);padding-left:10px;font-size:11.2px;line-height:17px;color:#555}

/* nav */
.main-nav{position:absolute;left:0;top:89px;width:1200px;height:63px;background:linear-gradient(var(--teal),var(--teal-dark))}
.main-nav ul{list-style:none;position:absolute;left:146px;top:22px;display:flex;gap:16px}
.main-nav a{color:#fff;font-size:11.5px;font-weight:600;text-decoration:none;text-transform:uppercase}
.main-nav a.active{border-bottom:2px solid #fff;padding-bottom:3px}
.search{position:absolute;left:853px;top:10px;width:208px;height:38px;background:#fff;border-radius:2px;font-size:12px;color:#bbb;padding:11px 14px}
.search svg{position:absolute;right:12px;top:11px}

/* hero */
.hero{position:absolute;left:0;top:152px;width:1200px;height:482px;background:linear-gradient(120deg,#7d7d7b 0%,#a9a9a6 30%,#d9d9d6 50%,#8f8e8b 75%,#5e5d5a 100%)}
.hero-shadow{position:absolute;left:200px;top:620px;width:800px;height:110px;background:radial-gradient(ellipse at 50% 0%,rgba(0,0,0,.22),rgba(0,0,0,0) 65%)}
.hero-caption{position:absolute;left:285px;top:376px;width:657px;height:199px;background:rgba(25,25,25,.82);text-align:center;color:#fff;padding-top:22px}
.hero-caption h1{font-size:35px;font-weight:700;line-height:44px;text-transform:uppercase;letter-spacing:.5px}
.hero-caption p{font-size:17px;line-height:26px;margin-top:12px;padding:0 20px}
.hero-arrow{position:absolute;top:366px;width:54px;height:50px;background:var(--teal);display:flex;align-items:center;justify-content:center}
.dots{position:absolute;left:572px;top:602px;display:flex;gap:5px}
.dots span{width:20px;height:20px;border-radius:50%;background:#fff;border:2px solid #ddd}
.dots span.on{background:var(--teal);border-color:#fff}

/* section titles */
.section-title{position:absolute;left:0;width:1200px;text-align:center;font-size:33px;color:var(--ink);font-weight:400}
.section-title b{font-weight:700}
.lead{position:absolute;left:215px;width:770px;text-align:center;font-size:14.5px;line-height:34px;color:var(--muted)}

/* services */
.service{position:absolute;top:965px;width:230px;text-align:center}
.service svg{display:block;margin:0 auto}
.service h3{font-size:21px;font-weight:400;color:#333;line-height:28px;margin-top:45px}

/* cards */
.cards{position:absolute;left:139px;width:924px;display:grid;grid-template-columns:repeat(4,213px);gap:24px}
.card .photo{height:133px}
.card h4{font-family:"Oswald",Arial,sans-serif;font-weight:300;font-size:23px;color:#4a4a4a;margin-top:15px;line-height:32px;white-space:nowrap;text-transform:uppercase}
.card p{font-size:11px;line-height:17.5px;color:var(--muted);margin-top:6px}
.btn-more{display:inline-block;margin-top:20px;width:120px;height:40px;border:2px solid #ccc;border-radius:5px;font-size:9px;text-align:center;line-height:36px;color:#888;text-transform:uppercase}

/* newsletter */
.newsletter{position:absolute;left:0;top:1821px;width:1200px;height:401px;background:linear-gradient(135deg,#434c5c,#3a4352 60%,#404a59)}
.newsletter h2{position:absolute;top:42px;width:1200px;text-align:center;color:#fff;font-size:31px;font-weight:400}
.newsletter h2 b{font-weight:700}
.newsletter .lead{top:110px;color:#b6bcc6;font-size:14px}
.field{position:absolute;top:209px;width:304px;height:51px;background:#fff;border-radius:3px;font-size:11px;color:#bbb;padding:18px 24px}
.btn{position:absolute;top:307px;height:50px;width:207px;border-radius:3px;color:#fff;font-size:11px;text-align:center;line-height:50px;text-transform:uppercase;letter-spacing:1px}
.btn.submit{left:382px;background:var(--sky)}
.btn.clear{left:615px;background:var(--teal)}

/* footer */
.site-footer{position:absolute;left:0;top:2730px;width:1200px;height:439px;background:var(--footer)}
.col{position:absolute;top:36px;width:212px}
.col h5{font-size:23px;font-weight:700;color:#fff;margin-bottom:22px}
.address{font-size:11px;line-height:22px;color:#d0d0d0}
.links{list-style:none}
.links li{font-size:11px;color:var(--teal);border-bottom:1px solid #444;line-height:30px}
.links li::before{content:"» ";color:#999}
.tweet{font-size:11.5px;line-height:20px;color:#d8d8d8;margin-bottom:14px}
.tweet span{color:var(--teal)}
.ffield{height:34px;background:#3c3c3c;margin-bottom:7px;font-size:10px;color:#aaa;padding:10px 14px}
.ffield.msg{height:76px}
.fsubmit{width:70px;height:32px;background:var(--teal);color:#fff;font-size:9px;text-align:center;line-height:32px;font-weight:600}
.copy-bar{position:absolute;left:0;top:367px;width:1200px;height:72px;background:var(--footer-bar);font-size:13px;color:#999;padding:24px 139px}
</style>
</head>
<body>

<header class="site-header">
  <div class="brand"><div class="name">CORAL</div><div class="sub">Web Development</div></div>
  <p class="tagline">Brisbane's leading web design &amp; website development company, specialising in search engine optimisation (SEO) &amp; content management systems (CMS).</p>
</header>

<nav class="main-nav">
  <ul>
    <li><a class="active" href="#">Home</a></li>
    <li><a href="#">About us</a></li>
    <li><a href="#">Services</a></li>
    <li><a href="#">Portfolio</a></li>
    <li><a href="#">Contact</a></li>
  </ul>
  <div class="search">Search
    <svg width="14" height="14" viewBox="0 0 14 14"><circle cx="6" cy="6" r="4.5" fill="none" stroke="#33b8a4" stroke-width="2"/><line x1="9.5" y1="9.5" x2="13" y2="13" stroke="#33b8a4" stroke-width="2"/></svg>
  </div>
</nav>

<section class="hero" role="img" aria-label="Businessman fitting large white puzzle pieces on a concrete wall"></section>
<div class="hero-shadow"></div>
<div class="hero-caption">
  <h1>We built your website<br>creative &amp; professional</h1>
  <p>Contrary to popular belief, Lorem Ipsum is not simply random text. It has roots in a piece of classical Latin literature from 45 BC.</p>
</div>
<div class="hero-arrow" style="left:139px"><svg width="20" height="24" viewBox="0 0 20 24"><polyline points="14,3 5,12 14,21" fill="none" stroke="#fff" stroke-width="3"/></svg></div>
<div class="hero-arrow" style="left:1007px"><svg width="20" height="24" viewBox="0 0 20 24"><polyline points="6,3 15,12 6,21" fill="none" stroke="#fff" stroke-width="3"/></svg></div>
<div class="dots"><span></span><span class="on"></span><span></span></div>

<h2 class="section-title" style="top:764px"><b>Who</b> we <b>are?</b></h2>
<p class="lead" style="top:820px">Contrary to popular belief, Lorem Ipsum is not simply random text. It has roots in a piece of classical Latin literature from 45 BC, making it over 2000 years old.</p>

<div class="service" style="left:117px">
  <svg width="192" height="192" viewBox="0 0 192 192">
    <circle cx="96" cy="96" r="86" fill="none" stroke="var(--ring)" stroke-width="18"/>
    <circle cx="96" cy="96" r="86" fill="none" stroke="var(--teal)" stroke-width="18" stroke-dasharray="405 540" transform="rotate(-90 96 96)"/>
    <rect x="62" y="68" width="66" height="50" rx="3" fill="none" stroke="#444" stroke-width="4"/>
    <line x1="62" y1="78" x2="128" y2="78" stroke="#444" stroke-width="4"/>
    <text x="70" y="102" font-family="Open Sans,sans-serif" font-size="14" font-weight="700" fill="#444">www</text>
    <circle cx="122" cy="118" r="11" fill="#fff" stroke="#444" stroke-width="3"/>
    <polyline points="116,118 121,123 128,113" fill="none" stroke="#444" stroke-width="3"/>
  </svg>
  <h3>Web Designing<br>&amp; Development</h3>
</div>
<div class="service" style="left:356px">
  <svg width="192" height="192" viewBox="0 0 192 192">
    <circle cx="96" cy="96" r="86" fill="none" stroke="var(--ring)" stroke-width="18"/>
    <circle cx="96" cy="96" r="86" fill="none" stroke="var(--teal)" stroke-width="18" stroke-dasharray="460 540" transform="rotate(-90 96 96)"/>
    <rect x="62" y="64" width="60" height="60" fill="none" stroke="#444" stroke-width="4"/>
    <line x1="72" y1="78" x2="110" y2="78" stroke="#444" stroke-width="4"/>
    <rect x="72" y="88" width="20" height="14" fill="#444"/>
    <circle cx="112" cy="110" r="13" fill="#fff" stroke="#444" stroke-width="4"/>
    <line x1="121" y1="119" x2="132" y2="130" stroke="#444" stroke-width="5"/>
  </svg>
  <h3>Search Engine<br>Optimization</h3>
</div>
<div class="service" style="left:603px">
  <svg width="192" height="192" viewBox="0 0 192 192">
    <circle cx="96" cy="96" r="86" fill="none" stroke="var(--ring)" stroke-width="18"/>
    <path d="M78 86 L96 64 L114 86" fill="none" stroke="#444" stroke-width="4"/>
    <rect x="60" y="86" width="72" height="10" fill="#444"/>
    <path d="M64 98 H128 L122 128 H70 Z" fill="#444"/>
    <g stroke="#fff" stroke-width="3"><line x1="80" y1="104" x2="80" y2="122"/><line x1="90" y1="104" x2="90" y2="122"/><line x1="100" y1="104" x2="100" y2="122"/><line x1="110" y1="104" x2="110" y2="122"/></g>
  </svg>
  <h3>E-Commerce<br>&nbsp;</h3>
</div>
<div class="service" style="left:851px">
  <svg width="192" height="192" viewBox="0 0 192 192">
    <circle cx="96" cy="96" r="86" fill="none" stroke="var(--ring)" stroke-width="18"/>
    <circle cx="96" cy="96" r="86" fill="none" stroke="var(--teal)" stroke-width="18" stroke-dasharray="515 540" transform="rotate(-90 96 96)"/>
    <rect x="72" y="60" width="38" height="72" rx="5" fill="none" stroke="#444" stroke-width="4"/>
    <circle cx="91" cy="124" r="3" fill="#444"/>
    <circle cx="112" cy="96" r="12" fill="#444"/>
    <g stroke="#444" stroke-width="5"><line x1="112" y1="79" x2="112" y2="113"/><line x1="95" y1="96" x2="129" y2="96"/><line x1="100" y1="84" x2="124" y2="108"/><line x1="124" y1="84" x2="100" y2="108"/></g>
    <circle cx="112" cy="96" r="5" fill="#fff"/>
  </svg>
  <h3>Phone &amp; Tablet<br>Applications</h3>
</div>

<h2 class="section-title" style="top:1351px"><b>Featured</b> Porfolio</h2>
<div class="cards" style="top:1422px">
  <article class="card"><div class="photo" role="img" aria-label="Website shown on several screens" style="background:linear-gradient(135deg,#e9edf3,#9fb0c4 60%,#3d4e66)"></div><h4>Lorem Ipsum Dummy</h4><p>Contrary to popular belief, Lorem Ipsum is not simply random text. It has roots in a piece of classical Latin literature from 45 BC, making it over 2000 years old.</p><span class="btn-more">Learn more</span></article>
  <article class="card"><div class="photo" role="img" aria-label="Tablet held over floating photo frames" style="background:linear-gradient(135deg,#f4f4f4,#cfd8e0 55%,#8a9aa8)"></div><h4>Lorem Ipsum Dummy</h4><p>Contrary to popular belief, Lorem Ipsum is not simply random text. It has roots in a piece of classical Latin literature from 45 BC, making it over 2000 years old.</p><span class="btn-more">Learn more</span></article>
  <article class="card"><div class="photo" role="img" aria-label="Rows of server screens in teal light" style="background:linear-gradient(180deg,#1b4d57,#3f9fa8 55%,#9fd5d8)"></div><h4>Lorem Ipsum Dummy</h4><p>Contrary to popular belief, Lorem Ipsum is not simply random text. It has roots in a piece of classical Latin literature from 45 BC, making it over 2000 years old.</p><span class="btn-more">Learn more</span></article>
  <article class="card"><div class="photo" role="img" aria-label="Laptop and phone on a blue digital background" style="background:linear-gradient(135deg,#1a5f91,#56a9d8 55%,#c5e4f3)"></div><h4>Lorem Ipsum Dummy</h4><p>Contrary to popular belief, Lorem Ipsum is not simply random text. It has roots in a piece of classical Latin literature from 45 BC, making it over 2000 years old.</p><span class="btn-more">Learn more</span></article>
</div>

<section class="newsletter">
  <h2>For latest update <b>join us</b> our Newsletter</h2>
  <p class="lead">Contrary to popular belief, Lorem Ipsum is not simply random text. It has roots in a piece of classical Latin literature from 45 BC, making it over 2000 years old.</p>
  <div class="field" style="left:112px">Name</div>
  <div class="field" style="left:434px">Email</div>
  <div class="field" style="left:757px">Country/City</div>
  <div class="btn submit">Submit</div>
  <div class="btn clear">Clear</div>
</section>

<h2 class="section-title" style="top:2283px"><b>News &amp;</b> Events</h2>
<div class="cards" style="top:2356px">
  <article class="card"><div class="photo" role="img" aria-label="Hand typing on a keyboard" style="background:linear-gradient(135deg,#f5f5f5,#bcc8d4 55%,#6f8398)"></div><h4>Lorem Ipsum Dummy</h4><p>Contrary to popular belief, Lorem Ipsum is not simply random text. It has roots in a piece of classical Latin literature from 45 BC, making it over 2000 years old.</p><span class="btn-more">Learn more</span></article>
  <article class="card"><div class="photo" role="img" aria-label="Business people assembling large puzzle pieces" style="background:linear-gradient(135deg,#fafafa,#d4d4d4 55%,#7c7c7c)"></div><h4>Lorem Ipsum Dummy</h4><p>Contrary to popular belief, Lorem Ipsum is not simply random text. It has roots in a piece of classical Latin literature from 45 BC, making it over 2000 years old.</p><span class="btn-more">Learn more</span></article>
  <article class="card"><div class="photo" role="img" aria-label="Silver robot figure" style="background:linear-gradient(135deg,#e6e9ea,#9aa4a8 55%,#4f5a5e)"></div><h4>Lorem Ipsum Dummy</h4><p>Contrary to popular belief, Lorem Ipsum is not simply random text. It has roots in a piece of classical Latin literature from 45 BC, making it over 2000 years old.</p><span class="btn-more">Learn more</span></article>
  <article class="card"><div class="photo" role="img" aria-label="Hand drawing on a glass screen" style="background:linear-gradient(135deg,#d9e3ea,#7f99ad 55%,#3c566b)"></div><h4>Lorem Ipsum Dummy</h4><p>Contrary to popular belief, Lorem Ipsum is not simply random text. It has roots in a piece of classical Latin literature from 45 BC, making it over 2000 years old.</p><span class="btn-more">Learn more</span></article>
</div>

<footer class="site-footer">
  <div class="col" style="left:139px">
    <h5>Contact</h5>
    <p class="address">Your Company Name<br><br>(Melbourne Office / Head Office)<br>Level 7, Suite 701 / 48 Harbour Lane<br>Melbourne, VIC 12345<br>Phone: (03) 5550 1234<br>(Brisbane Office)<br>Shop 1/112 Ridge Road,<br>Westvale, QLD 1234<br>(07) 5550 4567</p>
  </div>
  <div class="col" style="left:378px">
    <h5>Quick Links</h5>
    <ul class="links">
      <li>Lorem ipsum dolor sit</li><li>Amet consectetur</li><li>Praesent vel sem id</li><li>Curabitur hendrerit est</li><li>Aliquam eget erat nec sapien</li><li>Cras id augue nunc</li><li>Sed a nulla urna</li>
    </ul>
  </div>
  <div class="col" style="left:613px">
    <h5>Latest Tweets</h5>
    <p class="tweet"><span>@namehere</span> Justoid nonummy laoreet phasellent penatoque in antesque pellus elis eget tincidunt. Nequatdui laorem justo a non tellus laoremut vitae doloreet 1 day ago</p>
    <p class="tweet"><span>@namehere</span> Justoid nonummy laoreet phasellent penatoque in antesque pellus elis eget tincidunt. Nequatdui laorem justo a non tellus laoremut vitae doloreet 1 day ago</p>
  </div>
  <div class="col" style="left:849px">
    <h5>Contact Us</h5>
    <div class="ffield">Full Name</div>
    <div class="ffield">Email Address</div>
    <div class="ffield">Subject</div>
    <div class="ffield msg">Message</div>
    <div class="fsubmit">SUBMIT</div>
  </div>
  <div class="copy-bar">Copyright © 2015 Coral Web Development - All Rights Reserved</div>
</footer>

</body>
</html>
```